Website design for company that sells taximeters and has a taxi dispatch call center, webstore neede

Need a website with a shop with at least 20 articles, in two languages, possibly by using a purchased theme (not purchased yet).The company provides equipments and dispatch solutions for taxi companies. Typical yellow and black theme

Target Market(s)

Taxi companies

Industry/Entity Type

Taxi

Number of Pages Required

3 page

Font styles to use
Sans Serif

Colors
fbed22
000000

Requirements
Must have
• - webstore for at least 20 articles
• - Documents folder where to put pdf material related to taximeters
• - contact form message submission
Nice to have
• Feedback section
Should not have
• Blogs,

```html
<!DOCTYPE html>
<html lang="en">
<head>
<meta charset="utf-8">
<title>Metrona – Taximeters and Dispatch Equipment</title>
<link href="https://fonts.googleapis.com/css2?family=Montserrat:wght@400;500;600;700;800&family=Open+Sans:wght@400;600;700&display=swap" rel="stylesheet">
<style>
:root{
  --yellow:#f0c63c;
  --yellow-bright:#fbed22;
  --black:#000;
  --ink:#1d1d1d;
  --grey-text:#666;
  --light-grey:#f7f7f7;
  --line:#e4e4e4;
  --white:#fff;
}
*{margin:0;padding:0;box-sizing:border-box}
html,body{width:1200px;height:2553px;overflow:hidden;background:var(--white)}
body{position:relative;font-family:"Open Sans",Arial,sans-serif;color:var(--ink)}
.abs{position:absolute}

/* header */
.logo{left:150px;top:12px;font-family:"Montserrat",sans-serif;font-weight:800;font-size:25px;color:var(--yellow);letter-spacing:3px}
.nav{left:383px;top:20px;display:flex;gap:10px;font-family:"Montserrat",sans-serif;font-weight:700;font-size:10.5px;text-transform:uppercase;color:var(--ink)}
.nav .active{color:var(--yellow)}
.header-phone{left:755px;top:16px;display:flex;align-items:center;gap:10px;font-family:"Montserrat",sans-serif;font-weight:600;font-size:13px;letter-spacing:1.5px}
.lang{left:890px;top:21px;font-size:10px;font-weight:600}
.search{left:982px;top:14px;width:153px;height:28px;border:2px solid var(--yellow);border-radius:14px;font-size:11px;color:#bbb;padding:5px 14px;letter-spacing:1px}
.search svg{position:absolute;right:10px;top:6px}

/* hero */
.socials{left:177px;top:110px;display:flex;flex-direction:column;gap:15px}
.socials span{width:10px;height:10px;border-radius:50%;background:var(--ink);display:block}
.socials-label{left:172px;top:377px;transform:rotate(-90deg);transform-origin:left top;font-size:8px;font-weight:700;letter-spacing:1px;text-transform:uppercase;white-space:nowrap}
.hero-title{left:238px;top:152px;font-family:"Montserrat",sans-serif;font-weight:800;font-size:34px;letter-spacing:-0.5px;z-index:1}
.hero-bar{left:238px;top:184px;width:329px;height:13px;background:var(--yellow)}
.hero-sub{left:238px;top:204px;font-family:"Open Sans",sans-serif;font-size:30px;font-weight:400;letter-spacing:0.3px}
.hero-text{left:240px;top:255px;font-size:13px;line-height:18px;color:#444}
.btn-buy{left:240px;top:301px;width:111px;height:39px;border:3px solid var(--black);font-family:"Montserrat",sans-serif;font-weight:700;font-size:11px;letter-spacing:2px;display:flex;align-items:center;justify-content:center}
.hero-product{left:647px;top:152px;width:333px;height:197px;border-radius:6px;background:linear-gradient(180deg,#2a2a2a,#0d0d0d 70%,#dcdcdc)}
.slider-dots{left:1167px;top:224px;display:flex;flex-direction:column;gap:9px;align-items:center}
.slider-dots .on{width:12px;height:12px;border:2px solid var(--yellow);border-radius:50%;position:relative}
.slider-dots .on::after{content:"";position:absolute;left:2px;top:2px;width:4px;height:4px;border-radius:50%;background:var(--yellow)}
.slider-dots .off{width:8px;height:8px;border-radius:50%;background:var(--yellow)}
.hero-divider{left:603px;top:437px;width:2px;height:40px;background:var(--yellow)}
.hero-divider::after{content:"";position:absolute;left:-3px;top:16px;width:8px;height:8px;border-radius:50%;background:var(--yellow)}

/* about */
.about{left:0;top:477px;width:1200px;height:388px;background:var(--light-grey)}
.about-icon{left:582px;top:502px}
.about-title{left:0;top:550px;width:1200px;text-align:center;font-family:"Montserrat",sans-serif;font-weight:700;font-size:18px;letter-spacing:4px;color:var(--yellow)}
.about-text{left:270px;top:612px;width:660px;text-align:center;font-size:12.5px;font-weight:600;line-height:27px;letter-spacing:2.2px;color:#555;text-transform:uppercase}
.about-line{left:514px;top:817px;width:162px;height:1px;background:var(--yellow)}

/* deals */
.badge{left:243px;top:904px;padding:2px 6px;background:var(--yellow);color:var(--white);font-size:7.5px;font-weight:700;letter-spacing:0.5px;text-transform:uppercase}
.deal-title{left:243px;top:926px;font-family:"Montserrat",sans-serif;font-weight:500;font-size:19px;letter-spacing:1.8px;white-space:nowrap}
.deal-title b{font-weight:700}
.deal-title small{font-family:"Open Sans",sans-serif;font-size:7.5px;letter-spacing:1px;color:#777;vertical-align:middle;margin-left:4px}
.product-card{top:991px;width:222px;height:257px;border:1px solid var(--line);text-align:center}
.product-card .photo{margin:72px auto 0;width:144px;height:86px;border-radius:4px}
.product-card .name{margin-top:36px;font-size:9.5px;font-weight:600}
.product-card .stars{margin-top:6px;color:var(--yellow);font-size:11px;letter-spacing:1px}
.product-card .price{margin-top:3px;font-size:13px;color:#333}
.product-card .price s{font-size:10px;color:#999;margin-left:2px}
.pager{left:512px;top:1333px;width:184px;height:26px;border:2px solid var(--yellow);border-radius:13px;font-size:9.5px;letter-spacing:1px;display:flex;justify-content:space-between;align-items:center;padding:0 18px}
.pager-center{left:585px;top:1326px;width:38px;height:38px;border-radius:50%;background:var(--black);display:flex;align-items:center;justify-content:center}

/* banner */
.banner{left:0;top:1409px;width:1200px;height:443px;background:radial-gradient(ellipse at 50% 55%,#7a3a2a 0%,#3a2420 30%,#161616 70%,#0c0c0c)}
.banner-text{left:0;top:1661px;width:1200px;text-align:center;color:var(--white);font-family:"Montserrat",sans-serif;font-weight:700;font-size:18.5px;letter-spacing:3.2px}

/* testimonials */
.clients-title{left:0;top:1877px;width:1200px;text-align:center;font-family:"Montserrat",sans-serif;font-weight:700;font-size:19px}
.client-card{top:1942px;width:223px;height:184px;border:1px solid var(--line);text-align:center}
.client-card .avatar{width:42px;height:42px;border-radius:50%;background:linear-gradient(#c9c0b6,#7a6e66);margin:20px auto 0}
.client-card .who{margin-top:9px;font-family:"Montserrat",sans-serif;font-size:12px}
.client-card p{margin:6px 28px 0;font-size:8.5px;line-height:13px;color:#888}
.client-dots{left:594px;top:2156px;display:flex;gap:4px}
.client-dots span{width:7px;height:7px;border-radius:50%;background:#ddd}
.client-dots .on{background:var(--yellow)}

/* contact band */
.ask{left:0;top:2216px;width:1200px;height:102px;background:var(--yellow)}
.ask-text{left:192px;top:2255px;font-family:"Montserrat",sans-serif;font-weight:700;font-size:16px;color:var(--ink)}
.ask-text span{color:var(--white);margin-left:8px}
.ask-phone{left:647px;top:2252px;display:flex;align-items:center;gap:12px;font-family:"Montserrat",sans-serif;font-weight:700;font-size:18px;letter-spacing:1px}
.btn-feedback{left:841px;top:2245px;width:156px;height:37px;border:2px solid var(--white);color:var(--white);font-family:"Montserrat",sans-serif;font-weight:600;font-size:17px;letter-spacing:1.5px;display:flex;align-items:center;justify-content:center;gap:10px}

/* footer */
.footer{left:0;top:2318px;width:1200px;height:235px;background:#0b0b0b}
.foot-col{top:2358px;color:var(--white);font-size:9px;line-height:15px}
.foot-col h4{font-family:"Montserrat",sans-serif;font-size:9px;font-weight:700;margin-bottom:10px;text-transform:uppercase}
.foot-col h4 em,.foot-col .hl{color:var(--yellow);font-style:normal}
.foot-icons{display:flex;gap:6px}
.foot-icons span{width:9px;height:9px;border-radius:50%;background:var(--white)}
.foot-rule{left:252px;top:2458px;width:706px;height:1px;background:#444}
.copyright{left:252px;top:2469px;color:var(--white);font-size:8px}
.copyright .hl{color:var(--yellow)}
</style>
</head>
<body>

<header>
  <div class="abs logo">METRONA</div>
  <nav class="abs nav">
    <span class="active">Home</span><span>Shop</span><span>Services</span><span>Installers</span><span>Contact us</span><span>Join us</span>
  </nav>
  <div class="abs header-phone">
    <svg width="18" height="18" viewBox="0 0 24 24" fill="none" stroke="#1d1d1d" stroke-width="2"><path d="M22 16.9v3a2 2 0 0 1-2.2 2 19.8 19.8 0 0 1-8.6-3.1 19.5 19.5 0 0 1-6-6A19.8 19.8 0 0 1 2.1 4.2 2 2 0 0 1 4.1 2h3a2 2 0 0 1 2 1.7c.1.9.4 1.9.7 2.8a2 2 0 0 1-.5 2.1L8 9.9a16 16 0 0 0 6 6l1.3-1.3a2 2 0 0 1 2.1-.4c.9.3 1.9.6 2.8.7a2 2 0 0 1 1.7 2z"/></svg>
    555.010.4477
  </div>
  <div class="abs lang">ENG ∨</div>
  <div class="abs search">search
    <svg width="13" height="13" viewBox="0 0 24 24" fill="none" stroke="#ccc" stroke-width="2.5"><circle cx="10" cy="10" r="7"/><path d="M15 15l6 6"/></svg>
  </div>
</header>

<section class="hero">
  <div class="abs socials"><span></span><span></span><span></span><span></span><span></span></div>
  <div class="abs socials-label">Get in touch with socials</div>
  <div class="abs hero-bar"></div>
  <h1 class="abs hero-title">VEKTOR M3</h1>
  <div class="abs hero-sub">BLUETOOTH TAXIMETER</div>
  <p class="abs hero-text">Built in power supply and relay for toplights,<br>Built in signal divider.</p>
  <div class="abs btn-buy">BUY NOW</div>
  <div class="abs hero-product" role="img" aria-label="Product photo of a black taximeter with red fare display"></div>
  <div class="abs slider-dots"><span class="on"></span><span class="off"></span></div>
  <div class="abs hero-divider"></div>
</section>

<section>
  <div class="abs about"></div>
  <svg class="abs about-icon" width="36" height="24" viewBox="0 0 36 24" fill="none" stroke="#333" stroke-width="1.5">
    <rect x="14" y="1" width="8" height="4"/><path d="M8 10l3-5h14l3 5"/><rect x="3" y="10" width="30" height="8" rx="2"/><circle cx="10" cy="19" r="3"/><circle cx="26" cy="19" r="3"/>
  </svg>
  <h2 class="abs about-title">WHO WE ARE</h2>
  <p class="abs about-text">We supply the best meter &amp; dispatch<br>equipment for taxi vendors. Lorem ipsum dolor sit amet,<br>consectetuer adipiscing elit. Aenean commodo ligula eget dolor.<br>Aenean massa. Cum sociis natoque penatibus et magnis dis<br>parturient montes, nascetur ridiculus mus. Donec qu</p>
  <div class="abs about-line"></div>
</section>

<section>
  <div class="abs badge">Quality standard</div>
  <h2 class="abs deal-title"><b>DEAL</b> OF THE WEEK/ <small>EXCLUSIVE DISPATCH AND METER PRODUCTS</small></h2>

  <div class="abs product-card" style="left:248px">
    <div class="photo" role="img" aria-label="Photo of a dual display taximeter" style="background:linear-gradient(#555,#1a1a1a)"></div>
    <div class="name">Ipsum dolor sit amet conipiscing</div>
    <div class="stars">★★★★★</div>
    <div class="price">485.50$ <s>$720.20</s></div>
  </div>
  <div class="abs product-card" style="left:495px">
    <div class="photo" role="img" aria-label="Photo of a dispatch radio with handheld microphone" style="background:linear-gradient(#3a3a3a,#111)"></div>
    <div class="name">Ipsum dolor sit amet conipiscing</div>
    <div class="stars">★★★★★</div>
    <div class="price">456.50$ <s>$489.20</s></div>
  </div>
  <div class="abs product-card" style="left:742px">
    <div class="photo" role="img" aria-label="Photo of a compact taximeter with blue buttons" style="background:linear-gradient(#6a7a8a,#2a2f35)"></div>
    <div class="name">Ipsum dolor sit amet conipiscing</div>
    <div class="stars">★★★★★</div>
    <div class="price">450.50$ <s>$650.20</s></div>
  </div>

  <div class="abs pager"><span>&lt; PREV</span><span>NEXT &gt;</span></div>
  <div class="abs pager-center">
    <svg width="16" height="16" viewBox="0 0 16 16" fill="#f0c63c"><circle cx="3" cy="3" r="2"/><circle cx="8" cy="3" r="2"/><circle cx="13" cy="3" r="2"/><circle cx="3" cy="8" r="2"/><circle cx="8" cy="8" r="2"/><circle cx="13" cy="8" r="2"/><circle cx="3" cy="13" r="2"/><circle cx="8" cy="13" r="2"/><circle cx="13" cy="13" r="2"/></svg>
  </div>
</section>

<section>
  <div class="abs banner" role="img" aria-label="Night photo of a lit taxi roof sign against blurred city lights"></div>
  <h2 class="abs banner-text">ALL TAXI NEEDS FOR DRIVERS AND FLEETS</h2>
</section>

<section>
  <h2 class="abs clients-title">WHAT OUR CLIENTS SAY</h2>
  <div class="abs client-card" style="left:252px">
    <div class="avatar" role="img" aria-label="Client portrait"></div>
    <div class="who">Mia Lorne</div>
    <p>Sed malesuada, neque quis tincidunt suscipit, lorem lectus rutrum lacus, a iaculis ipsum eros sed ipsum. Sed scelerisque massa ut nibh tincidunt, eget pellentesque.</p>
  </div>
  <div class="abs client-card" style="left:494px">
    <div class="avatar" role="img" aria-label="Client portrait"></div>
    <div class="who">Sam Ortega</div>
    <p>Sed malesuada, neque quis tincidunt suscipit, lorem lectus rutrum lacus, a iaculis ipsum eros sed ipsum. Sed scelerisque massa ut nibh tincidunt, eget pellentesque.</p>
  </div>
  <div class="abs client-card" style="left:735px">
    <div class="avatar" role="img" aria-label="Client portrait"></div>
    <div class="who">Theo Marsh</div>
    <p>Sed malesuada, neque quis tincidunt suscipit, lorem lectus rutrum lacus, a iaculis ipsum eros sed ipsum. Sed scelerisque massa ut nibh tincidunt, eget pellentesque.</p>
  </div>
  <div class="abs client-dots"><span class="on"></span><span></span></div>
</section>

<section>
  <div class="abs ask"></div>
  <div class="abs ask-text">HAVE A QUESTION?<span>FEEL FREE TO ASK...</span></div>
  <div class="abs ask-phone">
    <svg width="22" height="22" viewBox="0 0 24 24" fill="none" stroke="#fff" stroke-width="2"><path d="M22 16.9v3a2 2 0 0 1-2.2 2 19.8 19.8 0 0 1-8.6-3.1 19.5 19.5 0 0 1-6-6A19.8 19.8 0 0 1 2.1 4.2 2 2 0 0 1 4.1 2h3a2 2 0 0 1 2 1.7c.1.9.4 1.9.7 2.8a2 2 0 0 1-.5 2.1L8 9.9a16 16 0 0 0 6 6l1.3-1.3a2 2 0 0 1 2.1-.4c.9.3 1.9.6 2.8.7a2 2 0 0 1 1.7 2z"/></svg>
    555.018.2230
  </div>
  <div class="abs btn-feedback">
    <svg width="28" height="20" viewBox="0 0 28 20" fill="#fff"><path d="M0 0h28v20H0z"/><path d="M1 1l13 10L27 1" fill="none" stroke="#f0c63c" stroke-width="2"/></svg>
    FEEDBACK
  </div>
</section>

<footer>
  <div class="abs footer"></div>
  <div class="abs foot-col" style="left:252px;width:170px">
    <h4>About <em>Metrona</em></h4>
    <p>We provide quality dispatch and meter equipment for indecent taxi &amp; fleet vendors.</p>
  </div>
  <div class="abs foot-col" style="left:434px">
    <h4>Contact info</h4>
    <p>Shop Office: (555) 014-2270<br>Customer service: (555) 017-3391<br>Email: <span class="hl">hello@metrona.example</span></p>
  </div>
  <div class="abs foot-col" style="left:614px">
    <h4>Hours of service</h4>
    <p>Monday - Friday: 09:00AM - 09:00PM<br>Saturday: 09:00AM - 07:00PM<br>Sunday: Closed</p>
  </div>
  <div class="abs foot-col" style="left:793px">
    <h4>Link <em>us</em></h4>
    <div class="foot-icons"><span></span><span></span><span></span><span></span><span></span></div>
  </div>
  <div class="abs foot-rule"></div>
  <div class="abs copyright">© 2018 <span class="hl">Metrona.example</span> &nbsp;&nbsp;&nbsp;| Trademarks and brands are the property of their respective owners.</div>
</footer>

</body>
</html>
```